Business Card Design Project

We are not a new company, but renamed to "Vantorin Kitchens" last year. We specialize in modern high-end cabinetry imports. We would like to communicate a sense of quality and cutting edge technology. Ideally the design would incorporate our logo colors, silver, red and preferably a black, matte background. Though we are open to suggestions.
Logo is attached.
Edit: I have attached rough drafts of the previous cards, this way you will have all necessary content that needs to go on the cards.
Updates
Project Deadline Extended
Reason: We have received a lot of great designs, but due to the sheer number we couldn't respond to all. We will extend the deadline for another 7 days to finalize and provide feedback to designers.
Thank you for your hard work!
Industry/Entity Type
Business
Look and feel
Each slider illustrates characteristics of the customer's brand and the style your logo design should communicate.

```html
<!DOCTYPE html>
<html lang="en">
<head>
<meta charset="utf-8">
<title>Vantorin Kitchens – Business Cards</title>
<link href="https://fonts.googleapis.com/css2?family=Michroma&family=Arimo:wght@400&family=PT+Sans&display=swap" rel="stylesheet">
<style>
  :root{
    --board:#8a5a34;
    --label:#2a1a0e;
    --card-black:#111213;
    --card-matte:#1c1d1f;
    --silver:#c4c6c8;
    --silver-light:#d9dadb;
    --silver-mid:#8a8c8e;
    --text-light:#e9e9e9;
    --red:#e3202a;
    --band-text:#ffffff;
  }
  html,body{margin:0;padding:0;overflow:hidden;}
  body{width:1200px;height:788px;background:var(--board);position:relative;}
  .view-label{
    position:absolute;width:526px;text-align:center;
    font-family:"PT Sans",sans-serif;font-size:22px;color:var(--label);
  }
  .card{
    position:absolute;width:526px;height:300px;border-radius:20px;overflow:hidden;
    background:radial-gradient(ellipse at 50% 30%, #2a2b2e 0%, var(--card-matte) 70%);
    box-shadow:0 4px 12px rgba(0,0,0,.45);
  }
  .card--gloss{background:radial-gradient(ellipse at 50% 35%, #1e1f21 0%, var(--card-black) 70%);}
  .wordmark{
    position:absolute;left:0;width:100%;text-align:center;
    font-family:"Michroma",sans-serif;color:var(--silver);letter-spacing:1px;
  }
  .contact-list{
    position:absolute;left:66px;top:156px;margin:0;padding:0;list-style:none;
    font-family:"Arimo",sans-serif;font-size:14px;color:var(--text-light);
  }
  .contact-list li{height:20px;display:flex;align-items:center;gap:6px;}
  .contact-list svg{width:12px;height:12px;fill:#8d8f92;}
  .address{
    position:absolute;left:346px;top:180px;
    font-family:"Arimo",sans-serif;font-size:14px;line-height:19px;color:var(--text-light);
  }
  .footer-band{
    position:absolute;left:0;bottom:0;width:100%;height:44px;
    background:linear-gradient(90deg, var(--red) 0%, var(--silver-mid) 30%, var(--silver-light) 100%);
  }
  .holder{
    position:absolute;bottom:14px;
    font-family:"Arimo",sans-serif;font-size:16px;color:var(--band-text);
  }
  .holder small{font-size:13px;}
  .texture{position:absolute;}
</style>
</head>
<body>

  <div class="view-label" style="left:52px;top:22px;">front</div>
  <div class="view-label" style="left:624px;top:22px;">front-1</div>
  <div class="view-label" style="left:55px;top:405px;">back</div>
  <div class="view-label" style="left:624px;top:405px;">Back - 1</div>

  <section class="card" style="left:52px;top:63px;">
    <div class="wordmark" style="top:92px;font-size:21px;">Vantorin Kitchens</div>
    <ul class="contact-list">
      <li><svg viewBox="0 0 12 12"><path d="M2 1l2 0 1 3-1.5 1a6 6 0 0 0 3.5 3.5L8 7l3 1v2c0 .6-.5 1-1 1C5 11 1 7 1 2c0-.5.4-1 1-1z"/></svg>555.210.0148</li>
      <li><svg viewBox="0 0 12 12"><path d="M3 1h5v3H3zM1 5h10v5H1z"/></svg>555.210.0176</li>
      <li><svg viewBox="0 0 12 12"><path d="M3.5 0h5v12h-5zM4.5 1.5v7h3v-7z"/></svg>555.388.4021</li>
      <li><svg viewBox="0 0 12 12"><path d="M1 3h10v7H1zM1 3l5 4 5-4"/></svg>marek@vantorinkitchens.ca</li>
    </ul>
    <div class="address">2817 - 64 St.<br>Halden<br>AB T3K 2P9</div>
    <div class="footer-band" role="img" aria-label="Decorative red and silver footer band"></div>
    <div class="holder" style="right:90px;">MAREK DOVAN, <small>President</small></div>
  </section>

  <section class="card card--gloss" style="left:624px;top:63px;">
    <div class="wordmark" style="top:92px;font-size:21px;">Vantorin Kitchens</div>
    <ul class="contact-list" style="left:50px;top:153px;">
      <li><svg viewBox="0 0 12 12"><path d="M2 1l2 0 1 3-1.5 1a6 6 0 0 0 3.5 3.5L8 7l3 1v2c0 .6-.5 1-1 1C5 11 1 7 1 2c0-.5.4-1 1-1z"/></svg>555.210.0148</li>
      <li><svg viewBox="0 0 12 12"><path d="M3 1h5v3H3zM1 5h10v5H1z"/></svg>555.210.0176</li>
      <li><svg viewBox="0 0 12 12"><path d="M3.5 0h5v12h-5zM4.5 1.5v7h3v-7z"/></svg>555.467.9302</li>
      <li><svg viewBox="0 0 12 12"><path d="M1 3h10v7H1zM1 3l5 4 5-4"/></svg>tomas@vantorinkitchens.ca</li>
    </ul>
    <div class="address" style="left:368px;top:176px;">2817 - 64 St.<br>Halden<br>AB T3K 2P9</div>
    <div class="footer-band" role="img" aria-label="Decorative red and silver footer band"></div>
    <div class="holder" style="right:78px;bottom:12px;">TOMAS DOVAN, <small>Director</small></div>
  </section>

  <section class="card" style="left:55px;top:447px;">
    <div class="wordmark" style="top:164px;font-size:24px;">Vantorin Kitchens</div>
  </section>

  <section class="card card--gloss" style="left:624px;top:447px;">
    <div class="texture" role="img" aria-label="Perforated metal dot texture, upper left"
         style="left:0;top:0;width:300px;height:90px;background:radial-gradient(ellipse at 50% 40%, #4a4b4e 0%, rgba(17,18,19,0) 70%);"></div>
    <div class="texture" role="img" aria-label="Perforated metal dot texture, lower right"
         style="right:0;bottom:0;width:260px;height:100px;background:radial-gradient(ellipse at 50% 60%, #4a4b4e 0%, rgba(17,18,19,0) 70%);"></div>
    <div class="wordmark" style="top:164px;font-size:24px;">Vantorin Kitchens</div>
  </section>

</body>
</html>
```